Telecommunications/Power civil contractor needs business card design

Were a new telecommunications/power underground civil contractor that is looking for a new business card design. Our company colours are silver or grey and orange. Feel free to use the white background logo or the black background logo.

Target Market(s)

Local contractors, utility companies, private sector mining/energy companies, developers.

Industry/Entity Type

Telecommunications

Contact Information for Business Card

Each card will need the following info:
Persons name:
Title:
E-mail:
Phone number:
Shop Address:
Mailing Address:

Requirements
Must have
• Each card will need the following info:
• Persons name:
• Title:
• E-mail:
• Phone number:
• Shop Address:
• Mailing Address:

```html
<!DOCTYPE html>
<html lang="en">
<head>
<meta charset="utf-8">
<title>Ridgeline Contracting Inc – Business Card</title>
<link rel="stylesheet" href="https://fonts.googleapis.com/css2?family=Source+Sans+3:wght@400;600;700;800&display=swap">
<style>
  :root {
    --bg: #8c8c8c;
    --paper: #f2f2f2;
    --orange: #cc4e20;
    --grey-dark: #555657;
    --grey-text: #5a5a5a;
    --grey-line: #9a9a9a;
    --white: #f4f4f4;
  }
  * { margin: 0; padding: 0; box-sizing: border-box; }
  html, body {
    width: 1105px; height: 1200px; overflow: hidden;
    background: var(--bg);
    font-family: "Source Sans 3", Arial, sans-serif;
  }
  .canvas { position: relative; width: 1105px; height: 1200px; }

  .card {
    position: absolute; left: 182px; width: 748px; height: 427px;
    overflow: hidden;
  }
  .card--front { top: 119px; background: var(--paper); }
  .card--back { top: 637px; background: var(--orange); }

  /* Front: brand block */
  .brand-mark {
    position: absolute; left: 148px; top: 105px;
    width: 124px; height: 124px;
    border: 7px solid var(--grey-dark); border-radius: 50%;
  }
  .brand-name {
    position: absolute; left: 40px; width: 340px; text-align: center;
    font-weight: 800; color: var(--grey-dark); line-height: 1;
  }
  .brand-name--main { top: 242px; font-size: 33px; letter-spacing: 1px; }
  .brand-name--sub { top: 280px; font-size: 17px; letter-spacing: 1.2px; }

  .divider {
    position: absolute; left: 377px; top: 62px;
    width: 1px; height: 292px; background: var(--grey-line);
  }

  /* Front: contact block */
  .contact { position: absolute; left: 421px; top: 62px; color: var(--grey-text); }
  .contact__name { font-size: 28px; font-weight: 600; color: var(--orange); line-height: 1.1; }
  .contact__title { font-size: 20px; line-height: 1.2; margin-top: 2px; }
  .contact__address { font-size: 20px; line-height: 27px; margin-top: 10px; }
  .contact__address + .contact__address { margin-top: 6px; }
  .contact__list { list-style: none; margin-top: 6px; }
  .contact__item { display: flex; align-items: center; font-size: 20px; line-height: 28px; }
  .contact__icon { width: 16px; height: 16px; margin-right: 12px; flex: none; }

  .band-line {
    position: absolute; left: 0; top: 390px; width: 100%; height: 3px;
    background: var(--grey-line);
  }
  .band {
    position: absolute; left: 0; top: 396px; width: 100%; height: 31px;
    background: var(--orange);
  }

  /* Back */
  .back-mark {
    position: absolute; left: 299px; top: 96px;
    width: 144px; height: 144px;
    border: 6px solid var(--white); border-radius: 50%;
  }
  .back-name {
    position: absolute; left: 0; width: 100%; text-align: center;
    font-weight: 800; color: var(--white); line-height: 1;
  }
  .back-name--main { top: 264px; font-size: 44px; letter-spacing: 1px; }
  .back-name--sub { top: 312px; font-size: 22px; letter-spacing: 1.5px; }
</style>
</head>
<body>
<div class="canvas">

  <section class="card card--front" aria-label="Business card front">
    <div class="brand-mark" aria-hidden="true"></div>
    <div class="brand-name brand-name--main">RIDGELINE</div>
    <div class="brand-name brand-name--sub">CONTRACTING INC</div>

    <div class="divider"></div>

    <div class="contact">
      <p class="contact__name">Dana Reyes</p>
      <p class="contact__title">CEO/Founder</p>
      <p class="contact__address contact__address--shop">1420 Birchwood Road<br>Fairbanks, Alaska 99701</p>
      <p class="contact__address contact__address--mailing">PO Box 3187<br>Fairbanks, Alaska 99707</p>
      <ul class="contact__list">
        <li class="contact__item">
          <svg class="contact__icon" viewBox="0 0 16 16" aria-hidden="true">
            <path fill="#cc4e20" d="M3.2 1.2l2.4 2.6-1.3 1.9c.9 2.2 2.9 4.3 5.9 5.9l1.9-1.3 2.6 2.4-1.6 2.1C7.3 14.6 1.6 8.9 1.1 2.8z"/>
          </svg>555 210 4836
        </li>
        <li class="contact__item">
          <svg class="contact__icon" viewBox="0 0 16 16" aria-hidden="true">
            <rect x="1" y="3" width="14" height="10" fill="#cc4e20"/>
            <path d="M1.5 3.5L8 9l6.5-5.5" fill="none" stroke="#f2f2f2" stroke-width="1.3"/>
          </svg>dana@ridgelinecivil.com
        </li>
        <li class="contact__item">
          <svg class="contact__icon" viewBox="0 0 16 16" aria-hidden="true">
            <circle cx="8" cy="8" r="7" fill="#cc4e20"/>
            <ellipse cx="8" cy="8" rx="3" ry="7" fill="none" stroke="#f2f2f2" stroke-width="1"/>
            <path d="M1 8h14" stroke="#f2f2f2" stroke-width="1"/>
          </svg>www.ridgelinecivil.com
        </li>
      </ul>
    </div>

    <div class="band-line"></div>
    <div class="band"></div>
  </section>

  <section class="card card--back" aria-label="Business card back">
    <div class="back-mark" aria-hidden="true"></div>
    <div class="back-name back-name--main">RIDGELINE</div>
    <div class="back-name back-name--sub">CONTRACTING INC</div>
  </section>

</div>
</body>
</html>
```